Federal IT Consulting Company - Brisolux Consulting Group

We're seeking a skilled web designer to create a modern, bold, and engaging WordPress website for Brisolux Consulting Group, LLC. Our company specializes in federal IT consulting, and our name is a play on "Brightening Solutions." The website should reflect our expertise in the federal technology marketplace and position us as a trusted partner for clients navigating their IT journey.

contact: info@brisoluxgrp-example.com

Current Status

WordPress is already installed on our hosting account
We have an existing logo (may need modernization)

Design Requirements

Style:

Modern and visually striking design
Bold elements to convey confidence and expertise
Incorporate the concept of "brightening solutions" into the design

Features:

Modern UX sliders for dynamic content presentation
Eye-catching, high-quality images (stock photos to be sourced by the designer)
Responsive design for all devices

Color Scheme:

To be proposed by the designer, should align with our brand and convey trust and technological expertise

Logo:

Evaluate our current logo
Create a transparent background version if needed
Propose modernization if deemed necessary

Accessibility:

Ensure design elements are accessible to users with disabilities
Use high contrast ratios for text and background colors
Provide text alternatives for non-text content

Website Structure
Create the following pages, with the possibility of subpages:

Home
Services
About
Contact

Specific Page Requirements
Home Page

Striking hero section with a clear value proposition
Overview of our services
Client testimonials or trust indicators

Services Page

Detailed list of our IT consulting services
Clear explanation of how we help navigate the federal IT landscape

About Page

Company history and mission
Team highlights (if applicable)
Our approach to federal IT consulting

Contact Page

Contact form
Other contact methods (phone, email)

Technical Requirements

Fully responsive design
SEO best practices implemented
Fast loading times
Integration with necessary plugins (to be discussed)
Training on how to update and maintain the site
Full compliance with Web Content Accessibility Guidelines (WCAG) 2.1 Level AA
Adherence to Section 508 standards for federal website accessibility
Implementation of necessary features for ADA compliance
Updates

Designs look the same

Target Market(s)

US Federal Govt customers looking for IT support.

Industry/Entity Type

IT Consulting

Coding

Coded - Design and coding required

Colors
0054AA
0677BA
7BADD7
CADEEF
E8F1F8
0094D4
00A9DD
6FCCEA
C7EBF8
E9F6FB
00AB8E
00BBA5
67D7C9
C6EFE9
E9F9F6

```html
<!DOCTYPE html>
<html lang="en">
<head>
<meta charset="UTF-8">
<title>Brisolux Federal Services</title>
<link href="https://fonts.googleapis.com/css2?family=Audiowide&family=Lato:wght@400;700&display=swap" rel="stylesheet">
<style>
:root{
  --blue:#00A9DD;
  --blue-deep:#0094D4;
  --ink:#1e1e1e;
  --text:#2b2b2b;
  --muted:#6b6b6b;
  --card:#F2F8FB;
  --dark:#444;
  --black:#000;
  --white:#fff;
  --star:#f2b63c;
}
*{box-sizing:border-box;margin:0;padding:0}
html,body{width:1200px;height:2819px;overflow:hidden}
body{font-family:'Lato',sans-serif;color:var(--text);background:var(--white);position:relative}
.display{font-family:'Audiowide',sans-serif}
.abs{position:absolute}

/* header */
.brand{font-family:'Audiowide',sans-serif;color:#2a3a48;font-size:36px;display:flex;align-items:center;gap:12px;letter-spacing:1px}
.brand .dot{width:22px;height:22px;border-radius:50%;background:var(--blue)}
.top-contact{display:flex;align-items:center;gap:12px;font-family:'Audiowide',sans-serif;font-size:15px;color:var(--ink)}
.ring{width:38px;height:38px;border:2px solid var(--blue);border-radius:50%;display:flex;align-items:center;justify-content:center}
.nav{top:101px;left:0;width:1200px;height:56px;background:var(--blue)}
.nav a{position:absolute;top:20px;font-family:'Audiowide',sans-serif;color:var(--white);font-size:14px;text-decoration:none}
.nav-call{position:absolute;left:868px;top:0;width:332px;height:56px;background:var(--dark);color:var(--white);font-family:'Audiowide',sans-serif;font-size:14px;padding:9px 0 0 51px;line-height:24px}
.nav-call-icon{position:absolute;left:848px;top:11px;width:36px;height:36px;border-radius:50%;background:var(--white);border:3px solid #d8d8d8;display:flex;align-items:center;justify-content:center}

/* hero */
.hero{top:157px;left:0;width:1200px;height:548px;background:linear-gradient(100deg,#3b3d40 0%,#6e747b 40%,#b9bcbf 62%,#8e959b 80%,#5e6870 100%)}
.hero-copy{left:110px;top:138px;color:var(--white)}
.hero-copy .small{font-size:24px;letter-spacing:2px}
.hero-copy .big{font-size:52px;margin-top:6px;letter-spacing:1px}
.hero-copy p{width:420px;font-size:14.5px;line-height:26px;margin-top:14px}
.btn-light{display:inline-block;margin-top:26px;background:var(--white);color:var(--blue);border-radius:26px 0 26px 26px;font-family:'Audiowide',sans-serif;font-size:17px;padding:15px 22px}

/* about */
.section-title{font-family:'Audiowide',sans-serif;font-size:38px;color:#2a2a2a;letter-spacing:1px}
.about-img{left:186px;top:868px;width:318px;height:318px;border-radius:50%;background:radial-gradient(circle,#c7cdd2 0%,#9aa3aa 55%,#6fa9c8 56%,#00A9DD 100%)}
.about-text{left:563px;top:843px;width:530px;font-size:16.5px;line-height:32px;text-align:justify;color:#222}
.about-text p+p{margin-top:32px}
.btn-blue{left:561px;top:1128px;width:180px;height:55px;background:var(--blue);color:var(--white);border-radius:28px 0 28px 28px;font-family:'Audiowide',sans-serif;font-size:17px;display:flex;align-items:center;justify-content:center}

/* services */
.services-band{top:1270px;left:0;width:1200px;height:285px;background:var(--blue)}
.service-frame{width:286px;height:362px;border:3px solid var(--white);top:1449px}
.service-card{width:286px;height:362px;top:1437px;background:var(--card);padding:20px 18px}
.service-card h3{font-family:'Audiowide',sans-serif;font-size:22px;line-height:37px;color:#1c1c1c;font-weight:400}
.service-icon{position:absolute;right:26px;top:26px;width:58px;height:58px;border-radius:50%;background:var(--white);display:flex;align-items:center;justify-content:center}
.service-card p{margin-top:24px;font-size:15.5px;line-height:31px;color:#333}
.service-card a{display:inline-block;margin-top:10px;color:var(--blue);font-size:15.5px;text-decoration:underline}

/* testimonials */
.t-card{top:1958px;width:300px;height:202px;background:var(--white);box-shadow:0 2px 10px rgba(0,0,0,.1);border-radius:4px;padding:14px 12px}
.avatar{position:absolute;left:10px;top:14px;width:64px;height:64px;border-radius:50%;background:linear-gradient(160deg,#d9dde1,#9aa3ab)}
.t-head{margin-left:85px}
.stars{color:var(--star);font-size:12px;letter-spacing:1px}
.t-name{font-size:18px;font-weight:700;color:#222;margin-top:4px}
.t-date{font-size:10px;color:#888;margin-top:6px}
.t-card p{margin-top:18px;font-size:13.5px;line-height:26px;color:var(--muted)}
.t-card.mid p{color:#333}
.arrow{top:2044px;width:32px;height:32px;border-radius:50%;display:flex;align-items:center;justify-content:center}

/* footer */
.footer{top:2237px;left:0;width:1200px;height:582px;background:var(--black);color:var(--white)}
.field{top:70px;width:178px;height:53px;background:var(--white);color:#444;font-size:15px;padding:17px 20px}
.submit{background:var(--blue);color:var(--white);text-align:center;padding-left:0;padding-right:0}
.rule{left:111px;width:978px;height:1px;background:#cfcfcf}
.f-brand{font-family:'Audiowide',sans-serif;font-size:34px;color:var(--white);display:flex;align-items:center;gap:12px}
.f-brand .dot{width:22px;height:22px;border-radius:50%;background:var(--blue)}
.f-col h4{font-family:'Audiowide',sans-serif;font-weight:400;font-size:17px;letter-spacing:.5px}
.f-col ul{list-style:none;margin-top:20px}
.f-col li{font-size:15px;height:34.5px;display:flex;align-items:flex-start;gap:10px}
.social{top:364px;width:32px;height:32px;border-radius:50%;background:var(--blue)}
.c-row{display:flex;gap:12px;font-size:15px;line-height:27px}
.c-ico{width:32px;height:32px;border-radius:50%;background:var(--blue);flex:none;display:flex;align-items:center;justify-content:center}
.copy{top:523px;left:0;width:1200px;text-align:center;font-size:15px}
</style>
</head>
<body>

<header>
  <div class="abs brand" style="left:110px;top:30px"><span class="dot"></span>BRISOLUX</div>
  <div class="abs top-contact" style="left:640px;top:31px">
    <span class="ring"><svg width="18" height="18" viewBox="0 0 24 24" fill="none" stroke="#00A9DD" stroke-width="2"><path d="M5 3h4l2 5-3 2a11 11 0 0 0 6 6l2-3 5 2v4a2 2 0 0 1-2 2A17 17 0 0 1 3 5a2 2 0 0 1 2-2z"/></svg></span>+1 555 010 0199
  </div>
  <div class="abs top-contact" style="left:875px;top:31px;font-size:14px">
    <span class="ring"><svg width="18" height="18" viewBox="0 0 24 24"><circle cx="12" cy="12" r="11" fill="#00A9DD"/><path d="M6 8h12v8H6z M6 8l6 5 6-5" fill="none" stroke="#fff" stroke-width="1.6"/></svg></span>info@brisoluxgrp-example.com
  </div>
</header>

<nav class="abs nav">
  <a style="left:110px">Home</a>
  <a style="left:252px">About Us</a>
  <a style="left:437px">Our Service</a>
  <a style="left:650px">Contact Us</a>
  <div class="nav-call">Call Us<br>+1 555 010 0199</div>
  <div class="nav-call-icon"><svg width="16" height="16" viewBox="0 0 24 24" fill="none" stroke="#555" stroke-width="2"><path d="M5 3h4l2 5-3 2a11 11 0 0 0 6 6l2-3 5 2v4a2 2 0 0 1-2 2A17 17 0 0 1 3 5a2 2 0 0 1 2-2z"/></svg></div>
</nav>

<section class="abs hero" role="img" aria-label="Photo of a smiling businesswoman in an office meeting with colleagues in the background">
  <div class="abs hero-copy">
    <div class="display small">WELCOME TO</div>
    <div class="display big">BRISOLUX</div>
    <p>Itaque earum rerum hic tenetur a sapiente delectus, ut aut reiciendis voluptatibus maiores alias consequatur aut perferendis doloribus asperiores repellat.</p>
    <span class="btn-light">Get Started</span>
  </div>
</section>

<section>
  <h2 class="abs section-title" style="left:0;width:1200px;text-align:center;top:762px">ABOUT BRISOLUX</h2>
  <div class="abs about-img" role="img" aria-label="Photo of a team of colleagues discussing work around a laptop, in a round frame"></div>
  <div class="abs about-text">
    <p>Itaque earum rerum hic tenetur a sapiente delectus, ut aut reiciendis voluptatibus maiores alias consequatur aut perferendis doloribus asperiores repellat.</p>
    <p>Duis aute irure dolor in reprehenderit in voluptate velit Duis aute irure m dolore eu fugiat nulla pariatur. Excepteur sint occaecat cupidatat non proident, sunt in culpa qui officia deserunt.esse cillum dolore eu fugiat nulla pariatur. Excepteur sint occan proident, sunt in culpa qui officia deserunt.</p>
  </div>
  <div class="abs btn-blue">Read More</div>
</section>

<section>
  <div class="abs services-band"></div>
  <h2 class="abs section-title" style="left:110px;top:1325px;color:var(--white)">OUR SERVICES</h2>

  <div class="abs service-frame" style="left:126px"></div>
  <div class="abs service-frame" style="left:465px"></div>
  <div class="abs service-frame" style="left:803px"></div>

  <div class="abs service-card" style="left:111px">
    <h3>IT<br>SERVICES</h3>
    <div class="service-icon"><svg width="36" height="36" viewBox="0 0 36 36" fill="none" stroke="#0677BA" stroke-width="1.6"><rect x="7" y="8" width="22" height="15" rx="1"/><path d="M3 27h30l-2 2H5z"/><circle cx="18" cy="15" r="4"/><path d="M16 15l1.5 1.5L20 13.5"/></svg></div>
    <p>Itaque earum rerum hic tenetur a sapiente delectus, ut aut reiciendis voluptatibus maiores alias volupt atibus maiores alias consequatur aut perferendis doloribus asperiores repellat.</p>
    <a>Learn More</a>
  </div>
  <div class="abs service-card" style="left:450px">
    <h3>CONSULTING<br>SERVICES</h3>
    <div class="service-icon"><svg width="36" height="36" viewBox="0 0 36 36" fill="none" stroke="#0677BA" stroke-width="1.6"><path d="M9 4h14l5 5v23H9z"/><path d="M14 27v-4M18 27v-7M22 27v-5"/><circle cx="18" cy="13" r="3"/></svg></div>
    <p>Itaque earum rerum hic tenetur a sapiente delectus, ut aut reiciendis voluptatibus maiores alias volupt atibus maiores alias consequatur aut perferendis doloribus asperiores repellat.</p>
    <a>Learn More</a>
  </div>
  <div class="abs service-card" style="left:788px">
    <h3>FEDERAL<br>SERVICES</h3>
    <div class="service-icon"><svg width="36" height="36" viewBox="0 0 36 36" fill="none" stroke="#0677BA" stroke-width="1.6"><path d="M8 5h16l4 4v22H8z"/><circle cx="18" cy="17" r="5"/><path d="M22 21l6 6M12 28h8"/></svg></div>
    <p>Itaque earum rerum hic tenetur a sapiente delectus, ut aut reiciendis voluptatibus maiores alias volupt atibus maiores alias consequatur aut perferendis doloribus asperiores repellat.</p>
    <a>Learn More</a>
  </div>
</section>

<section>
  <h2 class="abs section-title" style="left:0;width:1200px;text-align:center;top:1875px">WHAT CUSTOMER SAYS</h2>

  <div class="abs arrow" style="left:37px;background:#9a9a9a"><svg width="14" height="14" viewBox="0 0 14 14" fill="none" stroke="#fff" stroke-width="2"><path d="M9 2L4 7l5 5"/></svg></div>
  <div class="abs arrow" style="left:1124px;background:#000"><svg width="14" height="14" viewBox="0 0 14 14" fill="none" stroke="#fff" stroke-width="2"><path d="M5 2l5 5-5 5"/></svg></div>

  <div class="abs t-card" style="left:113px">
    <div class="avatar" role="img" aria-label="Portrait photo of the reviewer"></div>
    <div class="t-head"><div class="stars">★★★★★</div><div class="t-name">Marcus Delane</div><div class="t-date">April 12, 2023</div></div>
    <p>Temporibus autem quibusdam et aut officiis debitis aut rerum necessitatibus saepe eveniet ut et voluptates nt et moles tiae non recusandae.</p>
  </div>
  <div class="abs t-card mid" style="left:451px">
    <div class="avatar" role="img" aria-label="Portrait photo of the reviewer"></div>
    <div class="t-head"><div class="stars">★★★★★</div><div class="t-name">Ryan Colter</div><div class="t-date">March 3, 2023</div></div>
    <p>Itaque earum rerum hic tenetur a sapiente delectus, ut aut reiciendis voluptatibus maiores alias consequatur aut perferendis doloribus asperiores repellat.</p>
  </div>
  <div class="abs t-card" style="left:790px">
    <div class="avatar" role="img" aria-label="Portrait photo of the reviewer"></div>
    <div class="t-head"><div class="stars">★★★★★</div><div class="t-name">Clara Whitfield</div><div class="t-date">Augest 24, 2023</div></div>
    <p>Nam libero tempore, cum soluta nobis est eligendi optio cumque nihil impedit quo minus id quod maxime placeat facere maxime placea possimus.</p>
  </div>
</section>

<footer class="abs footer">
  <div class="abs field" style="left:110px">Name</div>
  <div class="abs field" style="left:310px">Email</div>
  <div class="abs field" style="left:510px">Phone Number</div>
  <div class="abs field" style="left:710px">Address</div>
  <div class="abs field submit" style="left:910px">Submit</div>

  <div class="abs rule" style="top:185px"></div>

  <div class="abs f-brand" style="left:115px;top:253px"><span class="dot"></span>BRISOLUX</div>
  <div class="abs social" style="left:111px"></div>
  <div class="abs social" style="left:168px"></div>
  <div class="abs social" style="left:227px"></div>
  <div class="abs social" style="left:284px"></div>

  <div class="abs f-col" style="left:456px;top:240px">
    <h4>QUICK LINKS</h4>
    <ul>
      <li>➔ Home</li><li>➔ About</li><li>➔ Services</li><li>➔ Testimonials</li><li>➔ Contact Us</li>
    </ul>
  </div>
  <div class="abs f-col" style="left:665px;top:240px">
    <h4>HELP LINKS</h4>
    <ul>
      <li>➔ FAQ</li><li>➔ Terms of use</li><li>➔ Privacy Policy</li><li>➔ Support Links</li><li>➔ Conditions</li>
    </ul>
  </div>
  <div class="abs f-col" style="left:875px;top:240px">
    <h4>CONTACT US</h4>
    <div class="c-row" style="margin-top:22px"><span class="c-ico"><svg width="14" height="16" viewBox="0 0 14 16"><path d="M7 0a6 6 0 0 1 6 6c0 4-6 10-6 10S1 10 1 6a6 6 0 0 1 6-6z" fill="#fff"/><circle cx="7" cy="6" r="2" fill="#00A9DD"/></svg></span><span>Brisolux<br>United States</span></div>
    <div class="c-row" style="margin-top:14px;align-items:center"><span class="c-ico"><svg width="14" height="14" viewBox="0 0 24 24" fill="none" stroke="#fff" stroke-width="2.4"><path d="M5 3h4l2 5-3 2a11 11 0 0 0 6 6l2-3 5 2v4a2 2 0 0 1-2 2A17 17 0 0 1 3 5a2 2 0 0 1 2-2z"/></svg></span>+1 555 010 0199</div>
    <div class="c-row" style="margin-top:18px;align-items:center"><span class="c-ico"><svg width="14" height="12" viewBox="0 0 14 12"><rect x="0" y="1" width="14" height="10" rx="1" fill="#fff"/><path d="M0 2l7 5 7-5" fill="none" stroke="#00A9DD" stroke-width="1.4"/></svg></span>info@brisoluxgrp-example.com</div>
  </div>

  <div class="abs rule" style="top:487px"></div>
  <div class="abs copy">Copyrights@2024.Brisolux.All Rights Reserved</div>
</footer>

</body>
</html>
```